Business card design needed

I run a Beautician studio (for 7 years now)
I offer
- Velmo Body Sugaring
- Ruby Glaze
- Nails
- Facials
- Manicure
- Foot Treatment
It might not be necessary to list all those treatments?
Maybe the link to the Website is sufficient?
I leave that up to you ...
(more info on www.FernAndDewByLenka.com.au)
Velmo BodySugaring is our biggest success, It replaces waxing.
I would like to incorporate the logo into the Business Card.
We had many complaints regarding our old Business Cards as the Phone Number was to small.
On the backside, we would like a "your next Appointment" section.
Looking forward to you Design, cheers ... Lenka
Industry/Entity Type
Business
Contact Information for Business Card
Fern by Dew by Lenka
14 Korrin Sqr 3942 Dandara
www.FernAndDewByLenka.com.au
03 9481 2267

```html
<!DOCTYPE html>
<html lang="en">
<head>
<meta charset="utf-8">
<title>Velmo Body Sugaring – Business Cards</title>
<link href="https://fonts.googleapis.com/css2?family=Cinzel:wght@500;600&family=Marcellus&family=Open+Sans:wght@400;600&display=swap" rel="stylesheet">
<style>
  :root {
    --board: #1b1b1b;
    --card: #ffffff;
    --ink: #2a2a2a;
    --grey: #4d4d4d;
    --green: #0c9a48;
    --orange: #e9572a;
    --yellow: #f6c928;
    --sun: #f29a1e;
    --line: #8a8a8a;
  }
  * { box-sizing: border-box; margin: 0; padding: 0; }
  html, body { width: 1200px; height: 728px; overflow: hidden; }
  body {
    background: var(--board);
    font-family: "Open Sans", Arial, sans-serif;
    color: var(--grey);
    position: relative;
  }
  .card {
    position: absolute;
    width: 542px;
    height: 308px;
    background: var(--card);
    overflow: hidden;
  }
  .card--front   { left: 41px;  top: 37px; }
  .card--hours   { left: 41px;  top: 380px; }
  .card--appt-a  { left: 616px; top: 37px; }
  .card--appt-b  { left: 624px; top: 384px; }

  /* brand block */
  .brand {
    position: absolute;
    left: 0; right: 0;
    display: flex;
    flex-direction: column;
    align-items: center;
  }
  .brand__dot {
    width: 64px; height: 64px;
    border-radius: 50%;
    background: var(--sun);
  }
  .brand__name {
    margin-top: 14px;
    font-family: "Cinzel", Georgia, serif;
    font-weight: 600;
    font-size: 25px;
    letter-spacing: 2px;
    color: var(--ink);
  }
  .card--front .brand { top: 26px; }
  .card--hours .brand { top: 30px; }

  /* front card bands */
  .band-name {
    position: absolute;
    left: 0; right: 0; top: 182px; height: 46px;
    background: var(--green);
    color: #fff;
    font-family: "Marcellus", Georgia, serif;
    font-size: 24px;
    letter-spacing: 2.5px;
    display: flex; align-items: center; justify-content: center;
  }
  .band-contact {
    position: absolute;
    left: 0; right: 0; top: 234px; bottom: 0;
    background: linear-gradient(90deg, var(--orange), var(--yellow));
    color: #fff;
    text-align: center;
    font-family: "Marcellus", Georgia, serif;
  }
  .band-contact__address {
    margin-top: 10px;
    font-size: 15px;
    letter-spacing: 2.5px;
  }
  .band-contact__row {
    margin-top: 12px;
    display: flex; justify-content: center; align-items: center; gap: 14px;
    font-size: 15px;
    letter-spacing: 0.8px;
  }
  .band-contact__item { display: flex; align-items: center; gap: 6px; }
  .band-contact__item svg { width: 14px; height: 14px; }

  /* hours card */
  .hours__web {
    position: absolute; top: 206px; left: 0; right: 0;
    text-align: center;
    font-size: 14px; letter-spacing: 2.5px; color: var(--ink);
  }
  .hours__title {
    position: absolute; top: 236px; left: 0; right: 0;
    text-align: center;
    font-weight: 600; font-size: 20px; letter-spacing: 1.5px;
  }
  .hours__times {
    position: absolute; top: 272px; left: 0; right: 0;
    text-align: center;
    font-size: 15px; font-weight: 600;
  }
  .hours__sep { color: #aaa; margin: 0 6px; font-weight: 400; }

  /* appointment cards */
  .appt__title {
    position: absolute; left: 35px; top: 54px;
    font-family: "Cinzel", Georgia, serif;
    font-weight: 600;
    font-size: 19px;
    color: var(--green);
    letter-spacing: 0.5px;
  }
  .appt__brand {
    position: absolute; left: 380px; top: 16px; width: 116px;
    display: flex; flex-direction: column; align-items: center;
  }
  .appt__brand .brand__dot { width: 40px; height: 40px; }
  .appt__brand .brand__name { margin-top: 8px; font-size: 12px; letter-spacing: 1px; text-align: center; line-height: 1.25; }
  .appt__watermark {
    position: absolute; left: 0; right: 0; top: 70px;
    display: flex; flex-direction: column; align-items: center;
    opacity: 0.05;
  }
  .appt__watermark .brand__dot { width: 130px; height: 130px; }
  .appt__watermark .brand__name { font-size: 34px; margin-top: 20px; }
  .field { position: absolute; font-size: 15px; color: var(--grey); white-space: nowrap; }
  .rule-dotted { position: absolute; border-bottom: 1px dotted var(--line); height: 0; }
  .rule { position: absolute; border-bottom: 1px solid var(--line); height: 0; }
  .box { position: absolute; border: 1px solid #555; height: 20px; background: transparent; }
  .day { position: absolute; font-size: 15px; font-weight: 600; color: var(--grey); }
  .appt__note {
    position: absolute; left: 35px; top: 256px; width: 466px;
    font-size: 12.5px; line-height: 19px; color: var(--ink);
  }
</style>
</head>
<body>

  <!-- Front -->
  <section class="card card--front">
    <div class="brand">
      <span class="brand__dot"></span>
      <span class="brand__name">Velmo Body Sugaring</span>
    </div>
    <div class="band-name">Fern by Dew by Lenka</div>
    <div class="band-contact">
      <p class="band-contact__address">14 Korrin Sqr 3942 Dandara</p>
      <div class="band-contact__row">
        <span class="band-contact__item">
          <svg viewBox="0 0 16 16" aria-hidden="true"><circle cx="8" cy="8" r="7" fill="none" stroke="#fff" stroke-width="1.4"/><path d="M5.5 4.5l1.6 1.4-.8 1.2c.5 1 1.3 1.8 2.3 2.3l1.2-.8 1.4 1.6-1.1 1.1c-2.6-.4-4.6-2.4-5-5z" fill="#fff"/></svg>
          03 9481 2267
        </span>
        <span class="band-contact__item">
          <svg viewBox="0 0 16 16" aria-hidden="true"><g fill="none" stroke="#fff" stroke-width="1.2"><circle cx="8" cy="8" r="6.5"/><ellipse cx="8" cy="8" rx="2.8" ry="6.5"/><path d="M1.5 8h13M2.6 4.6h10.8M2.6 11.4h10.8"/></g></svg>
          www.FernAndDewByLenka.com.au
        </span>
      </div>
    </div>
  </section>

  <!-- Back: hours -->
  <section class="card card--hours">
    <div class="brand">
      <span class="brand__dot"></span>
      <span class="brand__name">Velmo Body Sugaring</span>
    </div>
    <p class="hours__web">www.FernAndDewByLenka.com.au</p>
    <h2 class="hours__title">Hours of Operation</h2>
    <p class="hours__times">Mon - Fri: 8.00am - 6.30pm<span class="hours__sep">|</span>Saturday: 8.00am - 1.00pm</p>
  </section>

  <!-- Appointment card, version A -->
  <section class="card card--appt-a appointment">
    <div class="appt__brand">
      <span class="brand__dot"></span>
      <span class="brand__name">Velmo Body Sugaring</span>
    </div>
    <h2 class="appt__title">YOUR APPOINTMENT</h2>
    <span class="field" style="left:35px;top:89px">Name :</span>
    <span class="rule-dotted" style="left:96px;top:105px;width:298px"></span>
    <span class="field" style="left:35px;top:127px">Date :</span>
    <span class="rule" style="left:96px;top:144px;width:98px"></span>
    <span class="field" style="left:200px;top:127px">Time :</span>
    <span class="rule" style="left:247px;top:144px;width:92px"></span>
    <span class="field" style="left:341px;top:127px">am / pm</span>
    <span class="field" style="left:35px;top:166px">Next Appointment</span>
    <span class="box" style="left:181px;top:166px;width:97px"></span>
    <span class="box" style="left:311px;top:166px;width:97px"></span>
    <span class="day" style="left:35px;top:204px">MON</span>
    <span class="box" style="left:77px;top:204px;width:34px"></span>
    <span class="day" style="left:118px;top:204px">TUE</span>
    <span class="box" style="left:156px;top:204px;width:34px"></span>
    <span class="day" style="left:197px;top:204px">WED</span>
    <span class="box" style="left:240px;top:204px;width:34px"></span>
    <span class="day" style="left:282px;top:204px">THU</span>
    <span class="box" style="left:320px;top:204px;width:34px"></span>
    <span class="day" style="left:362px;top:204px">FRI</span>
    <span class="box" style="left:393px;top:204px;width:34px"></span>
    <span class="day" style="left:434px;top:204px">SAT</span>
    <span class="box" style="left:469px;top:204px;width:34px"></span>
    <p class="appt__note">It would be appreciated if 24 hours notice could be given if you are unable to attend an appointment</p>
  </section>

  <!-- Appointment card, version B -->
  <section class="card card--appt-b appointment">
    <div class="appt__watermark" aria-hidden="true">
      <span class="brand__dot"></span>
      <span class="brand__name">Velmo Body Sugaring</span>
    </div>
    <h2 class="appt__title">YOUR APPOINTMENT</h2>
    <span class="field" style="left:35px;top:89px">Name :</span>
    <span class="rule-dotted" style="left:96px;top:105px;width:298px"></span>
    <span class="field" style="left:35px;top:127px">Date :</span>
    <span class="rule" style="left:96px;top:144px;width:98px"></span>
    <span class="field" style="left:200px;top:127px">Time :</span>
    <span class="rule" style="left:247px;top:144px;width:92px"></span>
    <span class="field" style="left:341px;top:127px">am / pm</span>
    <span class="field" style="left:35px;top:166px">Next Appointment</span>
    <span class="box" style="left:181px;top:166px;width:97px"></span>
    <span class="box" style="left:311px;top:166px;width:97px"></span>
    <span class="day" style="left:35px;top:204px">MON</span>
    <span class="box" style="left:77px;top:204px;width:34px"></span>
    <span class="day" style="left:118px;top:204px">TUE</span>
    <span class="box" style="left:156px;top:204px;width:34px"></span>
    <span class="day" style="left:197px;top:204px">WED</span>
    <span class="box" style="left:240px;top:204px;width:34px"></span>
    <span class="day" style="left:282px;top:204px">THU</span>
    <span class="box" style="left:320px;top:204px;width:34px"></span>
    <span class="day" style="left:362px;top:204px">FRI</span>
    <span class="box" style="left:393px;top:204px;width:34px"></span>
    <span class="day" style="left:434px;top:204px">SAT</span>
    <span class="box" style="left:469px;top:204px;width:34px"></span>
    <p class="appt__note">It would be appreciated if 24 hours notice could be given if you are unable to attend an appointment</p>
  </section>

</body>
</html>
```